Vantor Finance Flyer Design

I would like a high res flyer designed for mass printing. It is for a mortgage and finance broking company in Sydney. We are called Vantor Finance. The wording i would like displayed is the following
Looking For Something Extra from your broker?
Vantor Finance can make all the difference
What we offer you is an extensive range of mortgage and finance products, including:
• Home Loans
• Investment Loans
• Low Doc Loans
• Vehicle Finance
• Equipment Finance
• Commercial Loans
• Refinance
Contact Us
Phone (02) 7342 5086
email info@vantorfinance.com.au
web www.vantorfinance.com.au

```html
<!DOCTYPE html>
<html lang="en">
<head>
<meta charset="utf-8">
<title>Vantor Finance Flyer</title>
<link rel="stylesheet" href="https://fonts.googleapis.com/css2?family=Lato:wght@300;400;700&family=Arimo:wght@700&display=swap">
<style>
  :root {
    --page-bg: #e9e9e9;
    --paper: #ffffff;
    --brand-grey: #4a4a4a;
    --accent-blue: #2a9fd6;
    --body-grey: #555a60;
    --navy: #1d3a66;
    --navy-text: #22385c;
    --photo-light: #f4f8fc;
    --photo-mid: #c9d8ea;
    --photo-deep: #3d5a8a;
  }
  * { margin: 0; padding: 0; box-sizing: border-box; }
  html, body { width: 918px; height: 1200px; overflow: hidden; }
  body { background: var(--page-bg); font-family: "Lato", sans-serif; position: relative; }

  .flyer {
    position: absolute; left: 130px; top: 135px;
    width: 658px; height: 930px;
    background: var(--paper); overflow: hidden;
    box-shadow: 0 2px 6px rgba(0,0,0,0.15);
  }
  .hero-photo {
    position: absolute; left: 0; top: 360px; width: 658px; height: 512px;
    background:
      linear-gradient(90deg, rgba(255,255,255,0) 55%, rgba(61,90,138,0.85) 75%, rgba(40,60,100,0.9) 90%, rgba(200,215,235,0.6) 100%),
      linear-gradient(180deg, var(--paper) 0%, var(--photo-light) 25%, var(--photo-mid) 100%);
  }
  .brand { position: absolute; left: 58px; top: 62px; }
  .brand-row { display: flex; align-items: center; gap: 10px; }
  .brand-mark { width: 40px; height: 40px; background: var(--brand-grey); }
  .brand-name { font-size: 42px; font-weight: 400; color: var(--brand-grey); line-height: 1; }
  .brand-tagline { font-size: 15px; color: var(--brand-grey); margin: 4px 0 0 50px; }

  .content { position: absolute; left: 112px; top: 152px; width: 500px; }
  .headline {
    font-size: 42px; font-weight: 300; color: var(--accent-blue);
    line-height: 36px; text-transform: uppercase; letter-spacing: 0.3px;
  }
  .subhead {
    margin-top: 14px; font-size: 20px; font-weight: 400;
    color: var(--accent-blue); text-transform: uppercase;
  }
  .intro { margin-top: 2px; font-size: 18px; line-height: 24px; color: var(--body-grey); }
  .products { list-style: none; margin-top: 12px; }
  .products li { font-size: 18px; line-height: 27px; color: var(--body-grey); }
  .products li::before { content: "\2022"; color: var(--accent-blue); margin-right: 6px; }

  .contact-label {
    position: absolute; left: 118px; top: 847px;
    font-family: "Arimo", sans-serif; font-weight: 700; font-size: 19px;
    color: var(--navy-text);
  }
  .contact-bar {
    position: absolute; left: 0; top: 872px; width: 658px; height: 58px;
    background: var(--navy); display: flex; align-items: center; justify-content: center;
    gap: 8px; font-family: "Arimo", sans-serif; font-weight: 700; font-size: 16.5px;
    color: #ffffff;
  }
  .contact-item { display: flex; align-items: center; gap: 6px; }
  .contact-icon { width: 15px; height: 15px; flex: none; }
</style>
</head>
<body>
  <main class="flyer">
    <div class="hero-photo" role="img" aria-label="Blurred photo of business people walking through a bright office corridor"></div>

    <header class="brand">
      <div class="brand-row">
        <span class="brand-mark"></span>
        <span class="brand-name">Vantor Finance</span>
      </div>
      <p class="brand-tagline">mortgage and finance broking services</p>
    </header>

    <section class="content">
      <h1 class="headline">Looking for<br>something extra<br>from your broker?</h1>
      <h2 class="subhead">Vantor Finance can make all the difference.</h2>
      <p class="intro">What we offer you is an extensive range of mortgage and finance products, including:</p>
      <ul class="products">
        <li>Home Loans</li>
        <li>Investment Loans</li>
        <li>Low Doc Loans</li>
        <li>Vehicle Finance</li>
        <li>Equipment Finance</li>
        <li>Commercial Loans</li>
        <li>Refinance</li>
      </ul>
    </section>

    <p class="contact-label">CONTACT US</p>
    <footer class="contact-bar">
      <span class="contact-item">
        <svg class="contact-icon" viewBox="0 0 16 16"><rect x="0.5" y="0.5" width="15" height="15" rx="2" fill="#fff"/><path d="M5 3.5h2.2v3H5.8c0 1.8.6 3.6 1.4 4.8H8.6v1.9H6.2C4.7 11.5 3.9 9 3.9 6.6 3.9 5.4 4.3 4.3 5 3.5z" fill="#1d3a66"/></svg>
        (02) 7342 5086
      </span>
      <span class="contact-item">
        <svg class="contact-icon" viewBox="0 0 16 16"><rect x="0.5" y="2.5" width="15" height="11" rx="2" fill="#fff"/><path d="M3 5l5 3.5L13 5" stroke="#1d3a66" stroke-width="1.5" fill="none"/></svg>
        info@vantorfinance.com.au
      </span>
      <span class="contact-item">
        <svg class="contact-icon" viewBox="0 0 16 16"><rect x="0.5" y="0.5" width="15" height="15" rx="2" fill="#fff"/><circle cx="8" cy="8" r="5" fill="none" stroke="#1d3a66" stroke-width="1.3"/><path d="M3 8h10M8 3c-2 2.7-2 7.3 0 10M8 3c2 2.7 2 7.3 0 10" stroke="#1d3a66" stroke-width="1" fill="none"/></svg>
        www.vantorfinance.com.au
      </span>
    </footer>
  </main>
</body>
</html>
```